Retail Sign for Houseplant Campaign

Sign will measure 3 to 4 foot tall by 22.2inches and place on rolling racks of houseplants for a retail promotion in The Birchwell Yard. The theme of the promotion will be "New Year, New You!" Selling points which should be on the sign are Houseplants give you a taste of nature, Houseplants boost air quality inside your home, Indoor plants reduce anxiety, Indoor plants make you more productive, Houseplants improve your concentration and memory.
Updates

Target Market(s)

People who love plants

Industry/Entity Type

Horticulture/ retail

Colors
00AB8E
00BBA5
67D7C9
C6EFE9
E9F9F6
59FF00
82FF00
B8FF75
E3FFCB
F4FFEA
FFF300
FFF600
FEFA6F
FFFEC7
FFFEE8

Requirements
Must have
• Must feel energetic and encourage people to buy plants. Should include 1-2 photos and the selling points listed

```html
<!DOCTYPE html>
<html lang="en">
<head>
<meta charset="utf-8">
<title>New Year, New You! – Houseplant Sign</title>
<link href="https://fonts.googleapis.com/css2?family=Alegreya:ital,wght@1,400&family=Montserrat:wght@500;700;800&display=swap" rel="stylesheet">
<style>
  :root {
    --title-teal: #0f6470;
    --bar-teal: #00ab8e;
    --panel-deep-teal: #138f7f;
    --panel-bright-teal: #00b49c;
    --panel-olive: #8a8428;
    --panel-green: #058a1e;
    --accent-teal: #00a98e;
    --maker-green: #3f5a34;
    --yard-orange: #f47a20;
    --paper: #ffffff;
    --rule: #d9d9d9;
  }
  * { margin: 0; padding: 0; box-sizing: border-box; }
  html, body { width: 740px; height: 1200px; overflow: hidden; background: var(--paper); }
  .sign { position: relative; width: 740px; height: 1200px; background: var(--paper); }

  .top-bar { position: absolute; left: 198px; top: 0; width: 336px; height: 12px; background: var(--bar-teal); }
  .headline {
    position: absolute; top: 44px; left: 0; width: 740px; text-align: center;
    font-family: "Montserrat", sans-serif; font-weight: 800; font-size: 51px;
    letter-spacing: -1px; color: var(--title-teal);
  }

  .grid { position: absolute; top: 147px; left: 0; width: 740px; display: grid;
    grid-template-columns: 370px 370px; grid-template-rows: 237px 239px 241px 240px; }
  .point { display: flex; align-items: center; justify-content: center; text-align: center;
    font-family: "Alegreya", serif; font-style: italic; font-size: 34px; line-height: 43px; color: #fff; padding: 0 20px; }
  .point--nature { background: var(--panel-deep-teal); }
  .point--air { background: var(--panel-bright-teal); }
  .point--calm { background: var(--panel-olive); font-size: 33px; }
  .point--focus { background: var(--panel-green); }

  .photo { width: 100%; height: 100%; }
  .photo--shelf { background: linear-gradient(135deg, #f2f4f3 0%, #e3e6e4 45%, #c9b49a 75%, #8e9092 100%); }
  .photo--monstera { background: linear-gradient(90deg, #6b5a48 0%, #eeeeee 30%, #f4f4f4 50%, #2f5a2a 75%, #1f3f20 100%); }
  .photo--watering { background: linear-gradient(120deg, #e8e8e6 0%, #cfcfcd 40%, #4a6e86 60%, #4c6a4c 85%, #8a9c96 100%); }
  .photo--relax { background: linear-gradient(160deg, #f6f6f4 0%, #e9ece8 40%, #e6c9c4 60%, #3d5478 85%, #d8d8d6 100%); }

  .edge-accent { position: absolute; width: 13px; height: 135px; }
  .edge-accent--r1 { right: 0; top: 196px; background: var(--accent-teal); }
  .edge-accent--l2 { left: 0; top: 436px; background: var(--accent-teal); }
  .edge-accent--r3 { right: 0; top: 676px; background: var(--panel-olive); }
  .edge-accent--l4 { left: 0; top: 915px; background: var(--panel-green); }

  .footer { position: absolute; top: 1104px; left: 0; width: 740px; height: 96px; }
  .brand { position: absolute; top: 22px; height: 44px; display: flex; align-items: center; gap: 10px;
    font-family: "Montserrat", sans-serif; font-weight: 700; font-size: 22px; white-space: nowrap; }
  .brand--maker { right: 386px; color: var(--maker-green); }
  .brand--yard { left: 388px; color: var(--yard-orange); }
  .brand-square { width: 40px; height: 40px; flex: none; }
  .brand--maker .brand-square { background: var(--maker-green); }
  .brand--yard .brand-square { background: var(--yard-orange); }
  .footer-rule { position: absolute; left: 370px; top: 22px; width: 1px; height: 44px; background: var(--rule); }
</style>
</head>
<body>
<main class="sign">
  <div class="top-bar"></div>
  <h1 class="headline">New Year, New You!</h1>

  <section class="grid">
    <p class="point point--nature">Houseplants<br>give you a taste<br>of nature</p>
    <div class="photo photo--shelf" role="img" aria-label="Woman placing a potted croton plant on a white shelf in a bright living room"></div>

    <div class="photo photo--monstera" role="img" aria-label="Smiling woman wiping the leaves of a large monstera plant"></div>
    <p class="point point--air">Houseplants<br>boost air quality<br>inside your home</p>

    <p class="point point--calm">Indoor plants<br>reduce anxiety,<br>Indoor plants make<br>you more productive</p>
    <div class="photo photo--watering" role="img" aria-label="Mother and daughter watering a snake plant with a turquoise watering can"></div>

    <div class="photo photo--relax" role="img" aria-label="Relaxed young woman sitting on the floor with a laptop surrounded by houseplants"></div>
    <p class="point point--focus">Houseplants<br>improve your<br>concentration<br>and memory</p>
  </section>

  <div class="edge-accent edge-accent--r1"></div>
  <div class="edge-accent edge-accent--l2"></div>
  <div class="edge-accent edge-accent--r3"></div>
  <div class="edge-accent edge-accent--l4"></div>

  <footer class="footer">
    <div class="brand brand--maker"><span class="brand-square"></span>Verdant Makers</div>
    <div class="footer-rule"></div>
    <div class="brand brand--yard"><span class="brand-square"></span>The Birchwell Yard</div>
  </footer>
</main>
</body>
</html>
```